Website Re-Design and Refresh

We are looking for a redesign of www.brightmeadow-example.com the deliverable is a graphic which will be used as a template for the main site.
The Logo will remain the same
The Video currently shown must be included in your submission
Search Element must be included, this should be better visible than it is currently
All navigation current on the left is to be moved to the right.
Top left column should be a “Quick Quotation” element. It should stand out and draw the eye as that is the conversion that we aim for on our site. This is the purpose of the site to attract these.
Add Testimonials navigation that users can click upon.
Below this element on the right “Recent Posts” should become Latest News”
We want users to see how much press coverage the site has had, the following UK’s news logos should be used Courier, Morning Ledger, NVR and The Wayfarer.
Please use the current text from our site but make some main features which we want to draw attention to. 5 points and use fake text, using a bullet point, icon, graphic or colour to make it stick out the most.
Large Guarantee, shown through a Seal graphic. An example of this type of style is attached.
Updates

Please note that as per the brief we want to havenews/contact forms down the left hand side of the page. This is to comply with “F”shapeeye pattern which shows that users look mostly on the left of webpages.

Please make the quick quotes more distinctive and use of thefields suggested in the brief.

As you appear to like using vivid colours, please see thefollowing examples we like of vivid colours.

 

http://media.tallcrane-example.com/cpw-sales/static/images/common/global_nav/nnp_03.png

http://media.tallcrane-example.com/cpw-sales/static/sections/homepage/2012_04/images/ban_big_promises.png

http://media.tallcrane-example.com/cpw-sales/static/images/landing_pages/mobile_phones/April_2012/mp_hero2_v3.jpg

http://media.tallcrane-example.com/cpw-sales/static/sections/upgrades/images/sidebanner_payg_upgrades.gif

Pleaseamend your designs so that they adhere to the following:

 

Thereis a quick quotation form, as per brief, next to the video positionedon the left, the video on the right so they are the first items the userssee. 

 

The"seal" guarantee should be top right and 

Newsand Testimonials should be on the right hand side

 

Inthe main content text area please use latin ipsom lorem text and put 5 bulletpoints in large writing and latin below. Such as:

 

Lorem Ipsum 

Lorem Ipsum 

Lorem Ipsum 

Lorem Ipsum 

Lorem Ipsum 

 

Lorem Ipsum is simply dummy text ofthe printing and typesetting industry. Lorem Ipsum has been the industry'sstandard dummy text ever since the 1500s, when an unknown printer took a galleyof type and scrambled it to make a type specimen book. It has survived not onlyfive centuries, but also the leap into electronic typesetting, remainingessentially unchanged. It was popularised in the 1960s with the release ofLetraset sheets containing Lorem Ipsum passages, and more recently with desktoppublishing software like Quorin SheetSmith including versions of Lorem Ipsum.

The following design is a good indication of style and the use of bright colors. Although the positioning of some elements is not as per the brief. 

Please see best deigns so far:

Target Market(s)

Business To Business

Industry/Entity Type

News

Requirements
Must have
• The Logo will remain the same
Top right should be a “Quick Quotation” element. It should stand out and draw the eye as that is the conversion that we aim for on our site. This is the purpose of the site to attract these.

```html
<!DOCTYPE html>
<html lang="en">
<head>
<meta charset="utf-8">
<title>Brightmeadow – Reputation Management</title>
<link rel="stylesheet" href="https://fonts.googleapis.com/css2?family=Ubuntu:ital,wght@0,400;0,500;0,700;1,700&family=Open+Sans:wght@400;600;700&display=swap">
<style>
:root{
  --green:#3f9e1c;
  --green-light:#6cc33a;
  --green-dark:#2b7a10;
  --green-text:#3c9a17;
  --ink:#222;
  --body:#333;
  --pill:#2e2e2e;
  --panel:#f3f7ee;
  --panel-edge:#b9cfa8;
  --footer:#6c6d74;
  --footer-text:#f1f1f1;
  --gold:#f2b705;
}
*{box-sizing:border-box;margin:0;padding:0}
html,body{width:895px;height:1200px;overflow:hidden;background:#fff}
body{position:relative;font-family:"Open Sans",Verdana,sans-serif;color:var(--body)}
.abs{position:absolute}

/* header */
.brand{left:88px;top:26px;display:flex;align-items:center;gap:8px;font-family:"Ubuntu",sans-serif;font-weight:700;font-size:30px;color:var(--ink);letter-spacing:-.5px}
.brand-mark{width:22px;height:22px;background:var(--green);border-radius:50%}
.quick-quote{left:645px;top:22px;width:159px;height:44px;border-radius:4px;background:linear-gradient(#6cc93b,#3c9a17);border:2px solid #1f5e0a;box-shadow:0 5px 6px rgba(0,0,0,.25);color:#fff;font-family:"Ubuntu",sans-serif;font-size:17px;display:flex;align-items:center;justify-content:center}

/* nav */
.nav-bar{left:0;top:86px;width:895px;height:37px;background:linear-gradient(#58b92c,#2f8c12)}
.search{left:82px;top:89px;width:166px;height:30px;background:#111;border-radius:2px;padding:5px;display:flex}
.search-btn{width:43px;height:20px;background:var(--green);border-radius:3px 0 0 3px;color:#fff;font-size:7.5px;font-weight:700;display:flex;align-items:center;justify-content:center;gap:2px}
.search-field{flex:1;height:20px;background:#fff;border-radius:0 3px 3px 0;font-size:6.5px;font-style:italic;color:#aaa;padding:6px 6px}
.nav{left:250px;top:86px;height:37px;display:flex;align-items:center}
.nav a{color:#fff;text-decoration:none;font-size:8.2px;font-weight:600;padding:0 9px;line-height:20px;border-left:1px solid rgba(255,255,255,.25)}
.nav a:first-child{border-left:0}

/* hero */
.hero{left:84px;top:124px;width:728px;height:279px;background:linear-gradient(#7fb8e4 0%,#cfe4ef 38%,#cfe3b0 62%,#8cc24a 100%);border:2px solid #eee}
.hero-shadow{left:100px;top:404px;width:700px;height:18px;background:radial-gradient(ellipse at top,rgba(0,0,0,.35),rgba(0,0,0,0) 70%)}
.video{left:148px;top:132px;width:292px;height:260px;border-radius:40px 40px 30px 30px;background:linear-gradient(#c99a5e,#9c6a33);}
.video-screen{left:170px;top:180px;width:248px;height:160px;border-radius:26px;background:linear-gradient(#c9d6df,#9fb1be)}
.hero-title{left:486px;top:200px;font-family:"Ubuntu",sans-serif;font-style:italic;font-weight:700;font-size:19px;line-height:19px;color:var(--green-text)}
.hero-copy{left:486px;top:249px;width:300px;font-size:9px;line-height:11.8px;color:#333}
.hero-copy p+p{margin-top:12px}
.btn-small{background:linear-gradient(#58b92c,#2f8c12);color:#fff;font-family:"Ubuntu",sans-serif;font-size:8px;padding:4px 4px;border-radius:2px;display:inline-block}
.hero-more{left:487px;top:328px}

/* features */
.feature{top:440px;width:166px}
.feature-icon{width:44px;height:50px;margin:0 auto;border-radius:6px}
.feature-title{margin-top:7px;height:24px;background:var(--pill);color:#fff;border-radius:12px;font-family:"Ubuntu",sans-serif;font-size:11.5px;display:flex;align-items:center;justify-content:center;white-space:nowrap}
.feature-copy{margin-top:15px;font-size:8.4px;line-height:10.6px;text-align:justify;color:#333}
.feature-copy p+p{margin-top:10px}
.read-more{margin-top:13px;height:28px;border-radius:3px;background:linear-gradient(#5dbd2f,#2f8c12);box-shadow:0 2px 3px rgba(0,0,0,.35);color:#fff;font-family:"Ubuntu",sans-serif;font-size:13px;display:flex;align-items:center;justify-content:center;gap:6px}
.read-more svg{width:15px;height:15px}

/* panels */
.panel{top:678px;height:250px;background:linear-gradient(#fff,var(--panel));border:4px solid var(--panel-edge)}
.panel-about{left:-4px;width:560px;border-left:0;border-radius:0 8px 8px 0}
.panel-news{left:565px;width:334px;border-right:0;border-radius:8px 0 0 8px}
.panel-heading{font-family:"Ubuntu",sans-serif;font-weight:500;font-size:29px;letter-spacing:-.5px;color:#333;display:flex;align-items:center;gap:8px}
.panel-heading .ico{width:46px;height:32px;border-radius:4px}
.about-heading{left:110px;top:704px}
.about-copy{left:110px;top:748px;width:411px;font-size:9.3px;line-height:11.7px;text-align:justify;color:#222}
.about-copy p+p{margin-top:11px}
.news-heading{left:592px;top:707px}
.news-list{left:590px;top:748px;width:197px}
.news-item{font-size:9.2px;line-height:11.8px;text-align:justify;color:#222}
.news-item+.news-item{margin-top:11px}
.news-thumb{float:left;width:28px;height:28px;margin:1px 4px 0 0;background:linear-gradient(#8a6a3a,#3a2c1e)}
.news-date{color:var(--green-text);font-weight:700;font-style:italic;font-size:9px;display:block}
.news-more{left:590px;top:888px}

/* press */
.press{top:970px;font-family:"Ubuntu",sans-serif;font-weight:700;color:#111;font-size:19px;white-space:nowrap}

/* footer */
.footer{left:0;top:1034px;width:895px;height:166px;background:linear-gradient(#77787f,var(--footer))}
.footer-col{top:1049px;list-style:none;font-size:8.8px;line-height:15px;color:var(--footer-text)}
.footer-rule{left:82px;top:1133px;width:550px;height:1px;background:rgba(255,255,255,.3)}
.copyright{left:93px;top:1141px;width:540px;font-size:8.6px;line-height:11px;color:#fff}
.social{left:93px;top:1168px;display:flex;align-items:center;gap:8px;color:#fff;font-size:9px;font-weight:600}
.social svg{width:22px;height:18px}
.seal{left:636px;top:1055px;width:168px;height:128px;border-radius:50%;background:radial-gradient(circle,#ffd84a 0%,var(--gold) 55%,#c98400 100%)}
</style>
</head>
<body>

<header>
  <div class="abs brand"><span class="brand-mark"></span>Brightmeadow</div>
  <a class="abs quick-quote">“Quick Qutation”</a>
</header>

<div class="abs nav-bar"></div>
<form class="abs search">
  <span class="search-btn">
    <svg width="8" height="8" viewBox="0 0 10 10"><circle cx="4" cy="4" r="3" fill="none" stroke="#fff" stroke-width="1.6"/><line x1="6" y1="6" x2="9.5" y2="9.5" stroke="#fff" stroke-width="1.8"/></svg>Search</span>
  <span class="search-field">Enter Your Keyword...</span>
</form>
<nav class="abs nav">
  <a>REPUTATION MANAGEMENT</a>
  <a>ONLINE REPUTATION MANAGEMENT – ORM</a>
  <a>BRAND PROTECTION</a>
  <a>PRICES</a>
  <a>TESTIMONIALS</a>
</nav>

<section>
  <div class="abs hero" role="img" aria-label="Sky and green meadow backdrop"></div>
  <div class="abs hero-shadow"></div>
  <div class="abs video" role="img" aria-label="Video player shaped like a wooden retro television"></div>
  <div class="abs video-screen" role="img" aria-label="Video screen showing website diagram"></div>
  <svg class="abs" style="left:264px;top:228px" width="64" height="64" viewBox="0 0 64 64">
    <circle cx="32" cy="32" r="31" fill="#1b1b1b"/><polygon points="24,17 48,32 24,47" fill="#7bd13c"/>
  </svg>
  <h1 class="abs hero-title">Place Your Business at the<br>top of Search Enginess</h1>
  <div class="abs hero-copy">
    <p>Lorem Ipsum is simply dummy text of the printing and typesetting industry. Lorem Ipsum has been the industry's standard dummy text ever since the 1500s.</p>
    <p>When an unknown printer took a galley of type and scrambled it to make a type specimen book.</p>
  </div>
  <a class="abs btn-small hero-more">Read More</a>
</section>

<section>
  <article class="abs feature" style="left:82px">
    <div class="feature-icon" role="img" aria-label="Filing cabinet icon" style="background:linear-gradient(#d8a35a,#8a5a25)"></div>
    <h2 class="feature-title">Reputation Management</h2>
    <div class="feature-copy"><p>Lorem Ipsum is simply dummy text of the printing and typesetting industry.</p><p>Lorem Ipsum has been the industry's standard dummy text ever since the 1500s.</p></div>
    <a class="read-more">read more <svg viewBox="0 0 16 16"><circle cx="8" cy="8" r="7.5" fill="#fff"/><path d="M4 8h6M8 5l3 3-3 3" stroke="#444" stroke-width="1.8" fill="none"/></svg></a>
  </article>
  <article class="abs feature" style="left:267px">
    <div class="feature-icon" role="img" aria-label="Document with globe icon" style="background:linear-gradient(#e8eef5,#3a7fc4)"></div>
    <h2 class="feature-title" style="font-size:10.5px">Online Reputation Management</h2>
    <div class="feature-copy"><p>Lorem Ipsum is simply dummy text of the printing and typesetting industry.</p><p>Lorem Ipsum has been the industry's standard dummy text ever since the 1500s.</p></div>
    <a class="read-more">read more <svg viewBox="0 0 16 16"><circle cx="8" cy="8" r="7.5" fill="#fff"/><path d="M4 8h6M8 5l3 3-3 3" stroke="#444" stroke-width="1.8" fill="none"/></svg></a>
  </article>
  <article class="abs feature" style="left:455px">
    <div class="feature-icon" role="img" aria-label="Two user silhouettes icon" style="background:linear-gradient(#4a8fe0,#1a1a1a)"></div>
    <h2 class="feature-title">Online Reputation</h2>
    <div class="feature-copy"><p>Lorem Ipsum is simply dummy text of the printing and typesetting industry.</p><p>Lorem Ipsum has been the industry's standard dummy text ever since the 1500s.</p></div>
    <a class="read-more">read more <svg viewBox="0 0 16 16"><circle cx="8" cy="8" r="7.5" fill="#fff"/><path d="M4 8h6M8 5l3 3-3 3" stroke="#444" stroke-width="1.8" fill="none"/></svg></a>
  </article>
  <article class="abs feature" style="left:644px">
    <div class="feature-icon" role="img" aria-label="Star award on stand icon" style="background:linear-gradient(#5aa6e8,#4a4f57)"></div>
    <h2 class="feature-title">Brand Protection</h2>
    <div class="feature-copy"><p>Lorem Ipsum is simply dummy text of the printing and typesetting industry.</p><p>Lorem Ipsum has been the industry's standard dummy text ever since the 1500s.</p></div>
    <a class="read-more">read more <svg viewBox="0 0 16 16"><circle cx="8" cy="8" r="7.5" fill="#fff"/><path d="M4 8h6M8 5l3 3-3 3" stroke="#444" stroke-width="1.8" fill="none"/></svg></a>
  </article>
</section>

<section>
  <div class="abs panel panel-about"></div>
  <h2 class="abs panel-heading about-heading">Only One Reputation <span class="ico" role="img" aria-label="Small house illustration" style="background:linear-gradient(#c9794a,#6d8f3a)"></span></h2>
  <div class="abs about-copy">
    <p>We understand that you only have one reputation and provide services to both monitor how you are perceived online and reputation management services to allow you to ensure that you are in control of how your business is perceived online.</p>
    <p>Reputation Management is not simply for those who have suffered negative perception previously, but for all businesses to ensure that the most valuable asset they have is protected: their Reputation.</p>
    <p>Brightmeadow Reputation Services is a web-based service which provides real-time data to businesses on how their brand, intellectual copyright and overall reputation are portrayed on the internet. By scanning the internet for target words or phrases, the name of business, product brands and the name of key individual a report based on the positive or negative nature of how the business is perceived is returned</p>
  </div>

  <div class="abs panel panel-news"></div>
  <h2 class="abs panel-heading news-heading">Latest News <span class="ico" role="img" aria-label="Folded newspaper illustration" style="width:36px;height:24px;background:linear-gradient(#f4f4f4,#9a9a9a)"></span></h2>
  <div class="abs news-list">
    <div class="news-item"><span class="news-thumb" role="img" aria-label="News photo"></span><span class="news-date">21-03-2012</span>Lorem Ipsum is simply dummy text of the printing and typesetting industry. Lorem Ipsum has been the industry's standard dummy text ever since the 1500s,</div>
    <div class="news-item"><span class="news-thumb" role="img" aria-label="News photo"></span><span class="news-date">21-03-2012</span>Lorem Ipsum is simply dummy text of the printing and typesetting industry. Lorem Ipsum has been the industry's standard dummy text ever since the 1500s,</div>
  </div>
  <a class="abs btn-small news-more">Read More</a>
</section>

<section>
  <div class="abs press" style="left:90px">Morning Ledger</div>
  <div class="abs press" style="left:312px">NVR</div>
  <div class="abs press" style="left:480px">The Wayfarer</div>
  <div class="abs press" style="left:661px">The Sunday Courier</div>
</section>

<footer>
  <div class="abs footer"></div>
  <ul class="abs footer-col" style="left:91px">
    <li>Reputation Management</li><li>Online Reputation Management – ORM</li><li>Brand Protection</li><li>Internet Online Defamation</li><li>Online Reputation</li>
  </ul>
  <ul class="abs footer-col" style="left:291px">
    <li>Pro-Active Reputation Management</li><li>About Brightmeadow</li><li>Authors</li><li>Contact</li><li>Reputation Monitoring</li>
  </ul>
  <ul class="abs footer-col" style="left:477px;top:1050px">
    <li>Reputation Correction</li><li>Prices</li><li>Privacy Policy</li><li>Terms and Conditions of use</li>
  </ul>
  <div class="abs footer-rule"></div>
  <p class="abs copyright">© Copyright Brightmeadow Reputation Services. All Rights Reserved All Rights Reserved | Vat 000123456 | 4th Floor Linden Court | Harbour Row | Eastmere | EM1 4QA</p>
  <div class="abs social">
    <span>Friendly</span><span>Chirper</span>
    <svg viewBox="0 0 22 18"><rect x="1" y="2" width="20" height="14" fill="none" stroke="#fff" stroke-width="2"/><path d="M1 2l10 8 10-8" fill="none" stroke="#fff" stroke-width="2"/></svg>
    <svg viewBox="0 0 22 18"><rect x="6" y="1" width="10" height="5" fill="#fff"/><rect x="2" y="6" width="18" height="8" fill="#fff"/><rect x="6" y="11" width="10" height="6" fill="#ddd"/></svg>
    <svg viewBox="0 0 22 18"><rect x="8" y="0" width="6" height="18" fill="#fff"/><rect x="2" y="6" width="18" height="6" fill="#fff"/></svg>
  </div>
  <div class="abs seal" role="img" aria-label="Gold satisfaction guarantee seal with red ribbon"></div>
</footer>

</body>
</html>
```